Brivolt Technologies business card design

We need a business card designed with our new logo. it would be great if the card could communicate it is a technology based company.

Target Market(s)

system integrators

Industry/Entity Type

technology, IOT

Contact Information for Business Card

Name, designation, Address, telephone number, email address

Requirements
Must have
• logo and company name
Nice to have
• something to do with technology

```html
<!DOCTYPE html>
<html lang="en">
<head>
<meta charset="utf-8">
<title>Brivolt Technologies — Business Card</title>
<link rel="stylesheet" href="https://fonts.googleapis.com/css2?family=Arimo:wght@400;700&display=swap">
<style>
  :root {
    --backdrop: #d9d8d5;
    --card: #353535;
    --accent: #f7931e;
    --ink-light: #ffffff;
    --ink-soft: #e6e6e6;
  }
  html, body {
    margin: 0;
    padding: 0;
    width: 1200px;
    height: 801px;
    overflow: hidden;
    background: var(--backdrop);
    font-family: "Arimo", Arial, sans-serif;
  }
  .stage {
    position: relative;
    width: 1200px;
    height: 801px;
    display: flex;
    align-items: center;
    justify-content: center;
    gap: 40px;
  }
  .card {
    position: relative;
    width: 540px;
    height: 308px;
    background: var(--card);
    border-bottom: 5px solid var(--accent);
    box-shadow: 0 10px 24px rgba(0,0,0,0.25);
    overflow: hidden;
  }

  /* Front */
  .card-front .brand {
    position: absolute;
    left: 32px;
    top: 132px;
    width: 220px;
    display: flex;
    align-items: center;
    gap: 10px;
  }
  .brand-square {
    flex: none;
    width: 22px;
    height: 22px;
    background: var(--accent);
  }
  .brand-name {
    color: var(--ink-light);
    font-weight: 700;
    font-size: 19px;
    line-height: 1.1;
    letter-spacing: 0.5px;
    text-transform: uppercase;
    white-space: nowrap;
  }
  .divider {
    position: absolute;
    left: 278px;
    top: 44px;
    width: 1px;
    height: 220px;
    background: var(--accent);
  }
  .contact {
    position: absolute;
    left: 300px;
    top: 44px;
    color: var(--ink-light);
    font-size: 12.5px;
    line-height: 1.4;
  }
  .person-name {
    margin: 0;
    color: var(--accent);
    font-size: 19px;
    font-weight: 700;
    text-transform: uppercase;
    letter-spacing: 0.3px;
  }
  .person-role { margin: 0 0 14px; color: var(--ink-soft); font-size: 13px; }
  .address { margin: 0 0 14px; }
  .contact-list { list-style: none; margin: 0; padding: 0; }
  .contact-list li { display: flex; align-items: center; gap: 7px; margin-bottom: 3px; }
  .contact-list svg { width: 11px; height: 11px; flex: none; }

  /* Back */
  .card-back .brand {
    position: absolute;
    right: 40px;
    bottom: 54px;
    display: flex;
    align-items: center;
    gap: 14px;
  }
  .card-back .brand-name { font-size: 36px; letter-spacing: 1px; text-align: right; }
  .card-back .brand-square { width: 34px; height: 34px; }
</style>
</head>
<body>
<main class="stage">
  <section class="card card-front" aria-label="Business card front">
    <div class="brand">
      <span class="brand-square"></span>
      <span class="brand-name">Brivolt<br>Technologies</span>
    </div>
    <div class="divider"></div>
    <div class="contact">
      <p class="person-name">Daniel Varga</p>
      <p class="person-role">CEO/Founder</p>
      <p class="address">2180 Street Name<br>Country Name AB 8754</p>
      <ul class="contact-list">
        <li>
          <svg viewBox="0 0 12 12"><path fill="#f7931e" d="M2.5 1h2l1 3-1.3 1a6 6 0 0 0 2.8 2.8l1-1.3 3 1v2A1.5 1.5 0 0 1 9.5 11 8.5 8.5 0 0 1 1 2.5 1.5 1.5 0 0 1 2.5 1z"/></svg>
          (123) 555-0148
        </li>
        <li>
          <svg viewBox="0 0 12 12"><rect x="0.5" y="2" width="11" height="8" fill="#f7931e"/><path d="M0.5 2 6 6.5 11.5 2" fill="none" stroke="#353535" stroke-width="1"/></svg>
          info@brivolttech.com
        </li>
        <li>
          <svg viewBox="0 0 12 12"><circle cx="6" cy="6" r="5" fill="none" stroke="#f7931e" stroke-width="1.2"/><path d="M1 6h10M6 1c-2.5 3-2.5 7 0 10M6 1c2.5 3 2.5 7 0 10" fill="none" stroke="#f7931e" stroke-width="1"/></svg>
          www.brivolttech.com
        </li>
      </ul>
    </div>
  </section>

  <section class="card card-back" aria-label="Business card back">
    <div class="brand">
      <span class="brand-square"></span>
      <span class="brand-name">Brivolt<br>Technologies</span>
    </div>
  </section>
</main>
</body>
</html>
```